Screen-Design für Website (Recruiting Agency)
Ich bin wirklich äußerst zufrieden mit der Arbeit und der Zusammenarbeit: tesmaruplin ist auf jeden meiner Wünsche eingegangen und hat mir auch geduldig die verschiedenesten Varianten erarbeitet, wenn ich mir mal die Vorstellungskraft fehlte. Die 5 Sterne sind mehr als verdient. __ I am really extremely satisfied with the work and the cooperation: tesmaruplin has responded to every one of my wishes and has also patiently worked out the most varied of variants for me when I lacked the imagination. The 5 stars are more than deserved.
Zielgruppe
An english version of the briefing can be found at the end
Briefing:
Kurzbeschreibung des Projektes
ich möchte ich mit einer Agentur für Recruiting zum Januar 2021 selbstständig machen und benötige für meine Website noch ein grundlegendes Screen-Design und Bilder, Kollagen und/oder Illustrationen für die verschiednen Textblöcke für zunächst vier Seiten , die die Inhalte transportieren sollen und 'Lust auf das Lesen der Texte' machen.
Ich lasse mich auch von euch Profis gerne beraten, wenn bspw. Überschriften fehlen, Call-to-Action-Elemente (bspw. Kontaktformulare) anders positioniert oder der Footer andere Inhalte enthalten sollte.
Ich benötige
Frühe Entwicklungs-/Konzeptphase als Entscheidungsgrundlage
Ein Screendesign (als PDF, JPG oder via pv.morlint.com-Webansicht) für eine der vier Seiten und die Entwicklung der dazugehörigen Bildelemente.
Am Ende des Prozesses:
- das Screendesign (als PDF, JPG oder via pv.morlint.com-Webansicht)
- Entwicklung der Bildelemente (Bilder, Kollagen oder Ilustrationen) für die verschiedenen Absätze aller vier Seiten
- webfähige Bild-Formate der einzelenen Elemente (Header, Hintergründe, Bilder) fü ride Wordpress-Umsetzung des Designs
Nachtrag 16.11.2020:
Da bereits mehrfach nachgefragt wurde, konkretisiere ich noch einmal den Ablauf (entschuldigt bitte die Verwirrung):
Ich möchte den Aufwand in der Konzeptionsphase für die teilnehmenden Designer so gering wie möglich halten, daher:
Erwarte ichzunächst ein Screendesign für eine einzige Seite . Auf dieser Basis möchte ich eine Entscheidung treffen können. Dieses Screendesign beinhaltet den grundlegenden Aufbau und das grundlegende Design der miren-Seite, die Elemente, Bilder und/oder Illustrationen, die zu dieser konkreten Seite gehören. Eventuell frage ich euch, ob ihr noch das eine oder andere an diesem Entwurf anpassen oder konkretieseren könntet.
Aufgabenstellung
An english version of the project description and goals can be found at the end
Projektbeschreibung und Ziele
Projekthintergrund
Der Vertrieb soll im Januar 2021 starten und dazu benötige ich eine professionelle Website, die die vorgenannten Zielgruppen „emotional“ zum Stöbern einlädt und neugierig auf mehr miren macht. Vertrauen schafft.
Den Dummy der Website (ein Wordpress-Theme (Varlow: https://bramuth.at/themes/varlow-overview/) mit den bereits finalen Texten finden Sie unter https://mi-kobalt.de.
Hier ist nichts „designt“, sondern dient erst einmal lediglich dazu, das Projekt und die Texte der Seiten zu transportieren und festzulegen. Also bitte nicht an den Anordnungen der Textblöcke, Farbwahl oder Schriftgrößen stören - das ist wirklich nur ein Dummy.
Konkret geht es bei diesem Auftrag um folgende vier Seiten:
_Home
_Stellenanzeigen Recruiting
_Performance Recrutiing
_Recruitment Insights
Alle weiteren Seiten (über uns, Blog, Impressum, usw.) sind exemplarisch zwar schon angelegt, werden aber zu einem späteren Zeitpunkt angegangen.
Ziele
An der Unterseite https://mi-kobalt.de/recruitment_insights/ möchte ich gerne dokumentieren, was ich genau benötige.
Die einzelnen Textblöcke der vier Unterseiten sollen durch Bilder, Collagen und/oder Illustrationen unterstützt werden, die Seite „auflockern“ und dem User helfen, schneller den jeweiligen Inhalt und seinen Vorteil zu erfassen (in der Hoffnung, dass er dann auch die dazugehörigen Texte liest).
Inspirierend fand ich bspw. Seiten wie,
https://www.quenvik.com/insights/
https://www.holdenfeld.com/recruiting-software/plexposts/,
https://www.bavorent.com/solutions/programmatic-job-advertising
https://pelzorix.com/
Wichtige Icons bzw. Logos, die mit der Branche und den Schaltkanälen in Verbindung stehen, habe ich Ihnen als PPT-Datei angehängt, falls Sie diese in einem Entwurf ve..

```html
<!DOCTYPE html>
<html lang="de">
<head>
<meta charset="utf-8">
<title>miren advisory – Stellenanzeigen Recruiting</title>
<link rel="stylesheet" href="https://fonts.googleapis.com/css2?family=Fira+Sans:wght@400;500;600&family=Source+Sans+3:wght@300;400;600&display=swap">
<style>
:root{
  --deep:#23095f;
  --ink:#1f0c55;
  --accent:#8a1ea3;
  --accent-dark:#6b1590;
  --text:#6b6b78;
  --light:#f3f3f5;
  --line:#e4e4ea;
  --white:#fff;
}
*{box-sizing:border-box;margin:0;padding:0}
html,body{width:1200px;height:3538px;overflow:hidden}
body{font-family:"Source Sans 3",sans-serif;color:var(--text);background:var(--white);position:relative}
h1,h2,h3,.heading{font-family:"Fira Sans",sans-serif}
/* top bar */
.topbar{height:36px;background:var(--deep);color:#fff;font-size:12px;font-weight:600;display:flex;justify-content:space-between;align-items:center;padding:0 63px}
.topbar span{display:flex;align-items:center;gap:8px}
/* nav */
.nav{height:56px;display:flex;align-items:center;justify-content:space-between;padding:0 63px;border-bottom:1px solid var(--line)}
.brand{font-family:"Fira Sans",sans-serif;font-size:26px;color:var(--ink);font-weight:500}
.menu{display:flex;gap:6px;font-size:13px;font-weight:600;color:var(--ink)}
.menu a{padding:7px 13px;color:inherit;text-decoration:none}
.menu a.active{background:var(--accent);color:#fff}
/* hero */
.hero{height:169px;background:linear-gradient(100deg,#fbeff0 0%,#ffffff 40%,#f6f4fb 60%,#dbe9f5 80%,#c8d4ee 100%);text-align:center;padding-top:28px}
.hero h1{font-size:40px;font-weight:500;color:var(--ink);letter-spacing:.3px}
.hero p{font-size:18px;color:#555;line-height:24px;margin-top:6px}
.intro{height:183px;border-bottom:1px solid var(--line);text-align:center;padding:43px 195px 0;font-size:21px;line-height:32px;color:#6a3aa8;font-weight:300}
.intro b{font-weight:400;color:var(--ink)}
/* feature rows */
.feature{position:absolute;left:148px;width:904px;display:flex;align-items:center;gap:24px}
.art{flex:0 0 380px;border-radius:6px}
.art-a{height:260px;background:linear-gradient(135deg,#f1ecfa,#e2dbf3 55%,#d9cff0)}
.art-b{height:255px;background:linear-gradient(135deg,#eef0f8,#ddd7f1 55%,#cfc3ee)}
.copy{flex:1}
.label{font-size:14px;font-weight:600;color:#777;margin-bottom:6px}
.copy h2{font-size:21px;font-weight:500;color:var(--ink);line-height:31px;margin-bottom:12px}
.copy p{font-size:13.5px;line-height:22.5px;margin-bottom:22px}
.checks{list-style:none;font-size:13.5px;line-height:22.5px;margin-bottom:24px}
.checks li{display:flex;gap:14px;align-items:flex-start}
.checks svg{flex:0 0 18px;margin-top:3px}
.btn{display:inline-block;background:var(--accent);color:#fff;font-size:13px;font-weight:600;padding:10px 16px;text-decoration:none}
.rule{position:absolute;left:148px;width:904px;height:1px;background:var(--line)}
/* CTA band */
.cta{position:absolute;top:1315px;left:0;width:1200px;height:385px;background:linear-gradient(120deg,#2a0a6e 0%,#3a1592 50%,#2d0f7a 100%)}
.cta-copy{position:absolute;left:148px;top:64px;width:430px;color:#fff}
.cta-copy h2{font-size:24px;font-weight:500;line-height:32px}
.cta-copy p{font-size:15.5px;line-height:24px;margin-top:26px;padding-left:4px}
.cta-badge{position:absolute;left:600px;top:58px;width:80px;height:80px;border-radius:50%;background:#fff;box-shadow:0 4px 14px rgba(0,0,0,.35);display:flex;align-items:center;justify-content:center}
.form{position:absolute;left:657px;top:34px;width:394px;height:316px;background:#fff;padding:18px 40px}
.form h3{font-size:24px;font-weight:500;color:var(--ink);margin-bottom:18px}
.field{background:#efefef;font-size:15px;color:#333;padding:0 16px;margin-bottom:12px}
.field.email{height:44px;line-height:44px}
.field.link{height:96px;padding-top:13px}
.submit{background:var(--accent);color:#fff;font-size:17px;font-weight:500;text-align:center;height:45px;line-height:45px}
/* knowledge */
.know{position:absolute;top:2787px;left:0;width:1200px;height:481px;background:var(--light)}
.know h2{text-align:center;font-size:23px;font-weight:500;color:var(--ink);margin-top:43px}
.cards{position:absolute;left:150px;top:90px;display:flex;gap:35px}
.card{width:277px;height:335px;background:#fff}
.card .pic{height:148px}
.pic-1{background:linear-gradient(180deg,#1f6fb3,#1a4f8f)}
.pic-2{background:linear-gradient(180deg,#eef3f6,#dfe7ec)}
.pic-3{background:linear-gradient(160deg,#58b9ec,#2f7fcd 60%,#e23d51)}
.card .body{padding:18px 26px}
.card h3{font-size:18px;font-weight:400;color:var(--ink);margin-bottom:12px}
.card p{font-size:12.5px;line-height:19.5px;margin-bottom:14px}
.card .btn{font-size:11px;padding:6px 11px}
/* footer */
.footer{position:absolute;top:3268px;left:0;width:1200px;height:270px;background:linear-gradient(180deg,#2b0c6d,#3a1789);color:#fff;font-size:12.5px}
.footer h4{font-family:"Fira Sans",sans-serif;font-weight:400;font-size:16px;margin-bottom:14px}
.fcol{position:absolute;top:42px}
.fcol ul{list-style:none;line-height:22px}
.fcol p{line-height:16px}
.social{display:flex;gap:22px;margin-top:24px;align-items:center}
.social span{width:14px;height:14px;border-radius:50%;background:#fff;display:block}
.copyright{position:absolute;left:150px;right:150px;bottom:0;height:45px;border-top:1px solid rgba(255,255,255,.18);text-align:center;line-height:45px;font-size:12.5px}
</style>
</head>
<body>

<header>
  <div class="topbar">
    <span><svg width="16" height="11" viewBox="0 0 16 11"><rect x=".5" y=".5" width="15" height="10" fill="none" stroke="#fff"/><path d="M.5.5 8 6l7.5-5.5" fill="none" stroke="#fff"/></svg>kontakt@miren-advisory.de</span>
    <span><svg width="13" height="13" viewBox="0 0 24 24"><path fill="#fff" d="M6.6 10.8a15 15 0 0 0 6.6 6.6l2.2-2.2c.3-.3.7-.4 1-.2 1.1.4 2.3.6 3.6.6.6 0 1 .4 1 1V20c0 .6-.4 1-1 1A17 17 0 0 1 3 4c0-.6.4-1 1-1h3.5c.6 0 1 .4 1 1 0 1.3.2 2.5.6 3.6.1.3 0 .7-.2 1z"/></svg>+49 6123 555 014</span>
  </div>
  <nav class="nav">
    <div class="brand">miren advisory</div>
    <div class="menu">
      <a href="#">Home</a><a class="active" href="#">Stellenanzeigen Recruiting</a><a href="#">Performance Recruiting</a><a href="#">Recruitment Insights</a><a href="#">Blog</a><a href="#">Kontakt</a>
    </div>
  </nav>
</header>

<section class="hero">
  <h1>Stellenanzeigen Recruiting</h1>
  <p>Holen Sie mehr aus Ihren Stellenanzeigen.<br>Finden Sie die besten Kandidaten in kürzester Zeit.</p>
</section>

<section class="intro">
  Eine Stellenanzeige ist Ihre Arbeitgebermarke in Miniaturformat – <b>attraktiv, glaubwürdig und informativ.</b> Aber: Sie muss gefunden werden. Nicht von irgendwem. Sondern vom richtigen Talent für Ihre offene Vakanzen.
</section>

<section class="feature" style="top:480px">
  <div class="art art-a" role="img" aria-label="Illustration: Team arbeitet an einem Analyse-Dashboard mit Diagrammen und Glühbirne"></div>
  <div class="copy">
    <div class="label">Recruitment Insights</div>
    <h2>Clevere Vorhersagen und Analysen für eine erfolgreiche Stellenbesetzung</h2>
    <p>Das Ziel – die besten Köpfe zu finden – ist klar. Aber der beste, effizienteste Weg dorthin meist nicht. Hier greifen unsere Recruitment Insights, denn Zahlen, Daten und Fakten sind unsere schärfsten Waffen im Wettbewerb um die Talente.</p>
    <p>Mit den miren Recruitment Insights zeigen wir Ihnen bereits vor einer Buchung</p>
    <ul class="checks">
      <li><svg width="18" height="14" viewBox="0 0 18 14"><path d="M1 7l5 5L17 1" fill="none" stroke="#6abf3a" stroke-width="2.2"/></svg>in welchen Kanälen Sie Ihren Wunschkandidaten zielgerichtet und effizient rekrutieren - und wo eher nicht.</li>
      <li><svg width="18" height="14" viewBox="0 0 18 14"><path d="M1 7l5 5L17 1" fill="none" stroke="#6abf3a" stroke-width="2.2"/></svg>wie Sie Ihre Anzeige mit kleinen Änderungen auf maximale „Performance“ ausrichten</li>
      <li><svg width="18" height="14" viewBox="0 0 18 14"><path d="M1 7l5 5L17 1" fill="none" stroke="#6abf3a" stroke-width="2.2"/></svg>wie viel Budget sich Ihr Wettbewerb „leistet“.</li>
    </ul>
    <a class="btn" href="#">mehr über Recruitment Insights</a>
  </div>
</section>

<div class="rule" style="top:947px"></div>

<section class="feature" style="top:1000px">
  <div class="copy" style="flex:0 0 502px">
    <div class="label">Data-Driven Multiposting</div>
    <h2>Vorkonfigurierte Anzeigenpakete waren gestern</h2>
    <p style="text-align:justify">Wenn alle Anbieter die leistungsstärksten Kanäle zu Paketen konfigurieren, dann sollten sich alle Multiposting-Angebote im Markt nahezu gleichen. Oder nicht?</p>
    <p style="text-align:justify">Jobbörsen, Nischen-Portale, Business-Netzwerke oder Special Interest-Seiten – miren ist unabhängig und empfiehlt nur die besten Kanäle für Ihre hochqualifizierten Wunschkandidaten: datenbasiert, nachweisbar und anhand ihrer Performance.</p>
  </div>
  <div class="art art-b" style="margin-left:30px" role="img" aria-label="Illustration: Personen vor Bildschirmen mit Stoppuhr und Auswertungen"></div>
</section>

<section class="cta">
  <div class="cta-copy">
    <h2>Bereit für mehr qualifizierte Bewerber und besser besetzte Stellen?<br>Dann lassen Sie uns gemeinsam neue Talentmärkte erschließen!</h2>
    <p>Alles was wir benötigen, ist der Link zu Ihrer Stellenanzeige und wir senden Ihnen Ihre Recuitment Insights zurück.<br>Kostenlos. Unverbindlich.</p>
  </div>
  <div class="cta-badge"><svg width="44" height="36" viewBox="0 0 44 36"><path d="M2 16 42 2 30 34 20 22z" fill="#8a1ea3"/><path d="M20 22 42 2 14 28z" fill="#5a1280"/></svg></div>
  <div class="form">
    <h3>Kostenlos und unverbindlich</h3>
    <div class="field email">E-Mail</div>
    <div class="field link">Link zu Ihrer Stellenanzeige*</div>
    <div class="submit">Jetzt Starten</div>
  </div>
</section>

<section class="feature" style="top:1770px">
  <div class="art art-a" role="img" aria-label="Illustration: Team arbeitet an einem Analyse-Dashboard mit Diagrammen und Glühbirne"></div>
  <div class="copy">
    <div class="label">Stellenanzeigen Targeting</div>
    <h2>Die Kunst, gefunden zu werden – und zwar von den Richtigen</h2>
    <p>Wer bei den Suchen seiner Wunschkandidaten keine Top-Platzierungen erzielt, verliert.</p>
    <p>miren überlässt das Feld nicht Ihren Wettbewerbern und sorgt dafür, dass Top-Kandidaten Ihre Stellenanzeigen auch finden.</p>
  </div>
</section>

<div class="rule" style="top:2073px"></div>

<section class="feature" style="top:2125px">
  <div class="copy" style="flex:0 0 502px">
    <div class="label">Add-On: Social Media Boost</div>
    <h2>Das ganze Internet als Jobbörse</h2>
    <p style="text-align:justify">miren boostet Ihre Stellenanzeigen als Sponsored Recruitment Ads zusätzlich in die relevanten sozialen Netzwerke, Videoportale und Display Networks. So erreichen Sie auch Ihren „nicht aktiv suchenden“ Wunschkandidaten: Zur richtigen Zeit, am richtigen Ort mit der richtigen Botschaft – KI-gestützt, vollautomatisiert und effizient.</p>
    <a class="btn" href="#">mehr zu Social Recruiting</a>
  </div>
  <div class="art art-b" style="margin-left:30px" role="img" aria-label="Illustration: Personen vor Bildschirmen mit Stoppuhr und Auswertungen"></div>
</section>

<div class="rule" style="top:2416px"></div>

<section class="feature" style="top:2470px">
  <div class="art art-a" role="img" aria-label="Illustration: Team arbeitet an einem Analyse-Dashboard mit Diagrammen und Glühbirne"></div>
  <div class="copy">
    <div class="label">Conversion Optimierung</div>
    <h2>Nach „post“ kommt nicht „pray“</h2>
    <p>miren hält die Performance Ihrer veröffentlichten Anzeigen im Blick, um eine bestmögliche Conversion hochwertiger Kandidaten zu erreichen – über die gesamte Laufzeit. Am Ende zählt nur das Ergebnis: Die besten Kandidaten und besetzte Stellen. Zu überschaubaren Kosten, weil Sie teure Mehrmalsschaltungen meist vermeiden.</p>
  </div>
</section>

<section class="know">
  <h2>Wissenswertes</h2>
  <div class="cards">
    <article class="card">
      <div class="pic pic-1" role="img" aria-label="Illustration: Geschäftsmann vor einer Menschenmenge"></div>
      <div class="body"><h3>Duis aute irure dolor</h3><p>Lorem ipsum dolor sit amet, consectetur adipiscing elit, sed do eiusmod tempor incididunt ut labore et dolore magna aliqua.</p><a class="btn" href="#">Learn More</a></div>
    </article>
    <article class="card">
      <div class="pic pic-2" role="img" aria-label="Illustration: Lupe und Hand wählen eine Person aus einer Reihe aus"></div>
      <div class="body"><h3>Duis aute irure dolor</h3><p>Lorem ipsum dolor sit amet, consectetur adipiscing elit, sed do eiusmod tempor incididunt ut labore et dolore magna aliqua.</p><a class="btn" href="#">Learn More</a></div>
    </article>
    <article class="card">
      <div class="pic pic-3" role="img" aria-label="Illustration: Mann blickt durch ein Fernrohr"></div>
      <div class="body"><h3>Duis aute irure dolor</h3><p>Lorem ipsum dolor sit amet, consectetur adipiscing elit, sed do eiusmod tempor incididunt ut labore et dolore magna aliqua.</p><a class="btn" href="#">Learn More</a></div>
    </article>
  </div>
</section>

<footer class="footer">
  <div class="fcol" style="left:151px">
    <h4>Wichtige Links</h4>
    <ul><li>Recruitment Insights</li><li>Performance Recruiting</li><li>Stellenanzeigen Recruiting</li><li>Blog</li></ul>
  </div>
  <div class="fcol" style="left:379px;top:73px">
    <ul><li>Datenschutz</li><li>Impressum</li><li>über uns</li><li>Kontakt</li></ul>
  </div>
  <div class="fcol" style="left:669px">
    <h4>KONTAKT</h4>
    <p>miren advisory UG<br>Lindenhof Str. 7<br>65344 Kiedrich am Rhein</p>
    <div class="social"><span></span><span></span><svg width="14" height="10" viewBox="0 0 14 10"><rect width="14" height="10" fill="#fff"/><path d="M0 0l7 5 7-5" fill="none" stroke="#2b0c6d"/></svg></div>
  </div>
  <div class="fcol" style="left:839px;top:73px">
    <p>Telefon +49 6123 555 014<br>E-Mail kontakt@miren-advisory.de</p>
  </div>
  <div class="copyright">Copyright © 2020. All rights reserved.</div>
</footer>

</body>
</html>
```